Local Flower Farm Needs Business Card Design

I need business cards designed for a flower farm based in Eudora, Kansas.
Business Info:
We are a local cut flower farm located in Eudora, Kansas, founded by Corinne Haldwick. What started as a passion for agriculture and search for more joy in daily life has blossomed into a small business dedicated to providing the community with beautiful, fresh, and sustainable flowers. We specialize in local, seasonal blooms, ensuring that every petal reflects the care and dedication we pour into our craft. Our mission is to deliver the highest quality flowers directly to our customers through local farmers markets and to florists who share our commitment to sustainability. Join us in celebrating the beauty of nature, one bloom at a time!
Contact Details:
Corinne Haldwick
Owner
Phone 913-555-0147
Facebook: Rosalind Thorpe Gardens
Instagram: @RosalindThorpeGardens
Website: RosalindThorpeGardens.example
Target Market(s)
Wholesale to Florists and Direct to Consumer via Farmers Market
Industry/Entity Type
Florist, Farm
Contact Information for Business Card
Name, Contact Info, Logo
Look and feel
Each slider illustrates characteristics of the customer's brand and the style your logo design should communicate.

```html
<!DOCTYPE html>
<html lang="en">
<head>
<meta charset="utf-8">
<title>Rosalind Thorpe Gardens – Business Card</title>
<link rel="stylesheet" href="https://fonts.googleapis.com/css2?family=Montserrat:wght@400;500;700&display=swap">
<style>
  :root {
    --ink: #0a272c;
    --forest: #0a272c;
    --paper: #ffffff;
    --backdrop: #a3a3a3;
    --emboss: #1d4a50;
    --emboss-line: #2d6a72;
  }
  * { margin: 0; padding: 0; box-sizing: border-box; }
  html, body { width: 1093px; height: 1200px; overflow: hidden; }
  body {
    background: var(--backdrop);
    font-family: "Montserrat", sans-serif;
    color: var(--ink);
    position: relative;
  }
  .card {
    position: absolute;
    left: 264px;
    width: 597px;
    height: 364px;
    overflow: hidden;
  }
  .card-front { top: 224px; background: var(--paper); }
  .card-back { top: 615px; height: 368px; background: var(--forest); }

  .identity { position: absolute; left: 26px; top: 46px; }
  .identity-name { font-weight: 700; font-size: 24px; line-height: 1.1; letter-spacing: 0.2px; }
  .identity-role { font-weight: 400; font-size: 14px; margin-top: 2px; }

  .contact-list { position: absolute; left: 26px; top: 252px; list-style: none; }
  .contact-item {
    display: flex; align-items: center; gap: 8px;
    font-size: 14px; font-weight: 400; height: 22px;
  }
  .contact-icon { width: 13px; height: 13px; flex: none; }

  .brand-band {
    position: absolute; left: 333px; top: 0;
    width: 211px; height: 100%;
    background: var(--forest);
  }
  .brand-seal {
    position: absolute; left: 325px; top: 90px;
    width: 226px; height: 226px; border-radius: 50%;
    background: var(--paper);
    display: flex; align-items: center; justify-content: center;
  }
  .brand-name {
    font-weight: 700; font-size: 19px; line-height: 1.25;
    text-align: center; color: var(--ink);
  }

  .back-seal {
    position: absolute; left: 159px; top: 52px;
    width: 280px; height: 280px; border-radius: 50%;
    border: 1px solid var(--emboss-line);
    display: flex; align-items: center; justify-content: center;
  }
  .back-name {
    font-weight: 700; font-size: 26px; line-height: 1.25;
    text-align: center; color: var(--emboss);
  }
</style>
</head>
<body>
  <section class="card card-front">
    <div class="identity">
      <h1 class="identity-name">Corinne Haldwick</h1>
      <p class="identity-role">Owner</p>
    </div>

    <ul class="contact-list">
      <li class="contact-item">
        <svg class="contact-icon" viewBox="0 0 24 24" aria-hidden="true"><path fill="#0a272c" d="M6.6 10.8a15.1 15.1 0 0 0 6.6 6.6l2.2-2.2c.3-.3.7-.4 1-.2 1.1.4 2.3.6 3.6.6.6 0 1 .4 1 1V20c0 .6-.4 1-1 1A17 17 0 0 1 3 4c0-.6.4-1 1-1h3.5c.6 0 1 .4 1 1 0 1.3.2 2.5.6 3.6.1.3 0 .7-.2 1z"/></svg>
        <span>913-555-0147</span>
      </li>
      <li class="contact-item">
        <svg class="contact-icon" viewBox="0 0 24 24" aria-hidden="true"><circle cx="12" cy="12" r="11" fill="#0a272c"/></svg>
        <span>Rosalind Thorpe Gardens</span>
      </li>
      <li class="contact-item">
        <svg class="contact-icon" viewBox="0 0 24 24" aria-hidden="true"><circle cx="12" cy="12" r="11" fill="#0a272c"/></svg>
        <span>@RosalindThorpeGardens</span>
      </li>
      <li class="contact-item">
        <svg class="contact-icon" viewBox="0 0 24 24" aria-hidden="true"><circle cx="12" cy="12" r="10" fill="none" stroke="#0a272c" stroke-width="2.4"/><path d="M2 12h20M12 2c3 3 3 17 0 20M12 2c-3 3-3 17 0 20" fill="none" stroke="#0a272c" stroke-width="1.8"/></svg>
        <span>www.RosalindThorpeGardens.example</span>
      </li>
    </ul>

    <div class="brand-band"></div>
    <div class="brand-seal">
      <p class="brand-name">Rosalind<br>Thorpe<br>Gardens</p>
    </div>
  </section>

  <section class="card card-back">
    <div class="back-seal">
      <p class="back-name">Rosalind<br>Thorpe<br>Gardens</p>
    </div>
  </section>
</body>
</html>
```